Create a memorable Web Design for real estate branding

we are a Minnepolis brokerage and boutique housing specialist with over 27 years of experience in the Global furnished housing industry, servicing the Greater Los Angeles area. Specializing in “warm environments” we offer a customized approach to satisfying our guests and client’s needs by offering a wide array of options in highly desirable areas. Additionally, Lantern Dwelling Partners offers assistance and expertise to home buyers, sellers and investors.

Industry/Entity Type

Real Estate

Number of Pages Required

1 page

Font styles to use
Serif
Sans Serif
Decorative

```html
<!DOCTYPE html>
<html lang="en">
<head>
<meta charset="utf-8">
<title>Lantern Dwelling Partners – Real Estate</title>
<link href="https://fonts.googleapis.com/css2?family=Open+Sans:wght@400;600;700&display=swap" rel="stylesheet">
<style>
:root{
  --green:#8dc63f;
  --green-dark:#6fa62a;
  --ink:#2b2b2b;
  --ink-2:#222;
  --ink-3:#1b1b1b;
  --grey:#6d6d6d;
  --light:#f3f3f3;
  --line:#d8d8d8;
  --white:#fff;
}
*{box-sizing:border-box;margin:0;padding:0}
html,body{width:1200px;height:5308px;overflow:hidden}
body{font-family:"Open Sans",Arial,sans-serif;color:var(--ink);background:var(--white);position:relative;font-size:12px}
.section{position:absolute;left:0;width:1200px}
.abs{position:absolute}

/* top bar */
.topbar{top:0;height:32px;background:#f7f7f7;border-bottom:1px solid #e6e6e6}
.topbar .contact{left:160px;top:8px;font-size:11px;color:var(--grey);display:flex;gap:22px}
.topbar .contact span{display:flex;align-items:center;gap:6px}
.social{display:flex;gap:6px}
.social i{width:18px;height:18px;border-radius:50%;background:var(--green);display:block}
.topbar .social{position:absolute;right:160px;top:7px}

/* nav */
.nav{top:32px;height:80px;background:var(--white)}
.logo{left:160px;top:18px}
.logo b{display:block;font-size:24px;font-weight:700;color:var(--green);line-height:1}
.logo small{display:block;font-size:11px;color:var(--grey);margin-top:4px;letter-spacing:1px}
.menu{right:160px;top:30px;display:flex;gap:22px;font-size:11px;font-weight:700;color:var(--ink)}
.menu a{position:relative;text-decoration:none;color:inherit}
.menu a.active:after{content:"";position:absolute;left:0;right:0;top:22px;height:3px;background:var(--green)}

/* hero */
.hero{top:112px;height:608px;background:linear-gradient(180deg,#aebfd3 0%,#c9d3dc 45%,#8fa07a 75%,#4f6a3a 100%)}
.hero .arrow{top:250px;width:22px;height:30px;background:rgba(0,0,0,.45)}
.hero .arrow.right{right:0;background:var(--green)}
.caption{position:absolute;left:340px;top:348px;width:520px;height:84px;background:rgba(30,30,30,.7);text-align:center;padding-top:10px}
.caption h2{font-size:30px;font-weight:400;color:var(--green);line-height:1.2}
.caption p{font-size:11px;color:#eee;line-height:1.4;margin-top:4px}
.dots{display:flex;gap:6px;justify-content:center}
.dots i{width:8px;height:8px;border-radius:50%;border:1px solid var(--green);display:block}
.dots i.on{background:var(--green)}
.hero .dots{position:absolute;left:0;right:0;top:446px}

/* section titles */
.title{position:absolute;left:160px;width:880px;text-align:center}
.title h2{font-size:28px;font-weight:400;display:flex;align-items:center;gap:20px;line-height:1.2}
.title h2:before,.title h2:after{content:"";flex:1;height:2px;background:currentColor;opacity:.8}
.title p{font-size:11px;line-height:1.5;margin-top:8px;color:var(--grey)}
.dark .title p,.green .title p{color:inherit}

/* projects */
.projects{top:720px;height:900px;background:var(--white)}
.filters{position:absolute;left:0;right:0;top:204px;display:flex;justify-content:center;gap:6px}
.filters span{border:1px solid var(--line);font-size:10px;padding:4px 10px;color:var(--grey)}
.filters span.on{background:var(--green);border-color:var(--green);color:var(--white)}
.grid{left:160px;top:260px;width:880px;display:grid;grid-template-columns:repeat(3,1fr);gap:4px}
.grid div{height:232px;background:linear-gradient(135deg,#9a9a9a,#4d4d4d)}
.grid div:nth-child(2n){background:linear-gradient(135deg,#c2c2c2,#5e5e5e)}
.grid .hover{background:#2a2a2a !important;display:flex;align-items:center;justify-content:center;gap:10px}
.loadmore{left:0;right:0;text-align:center;font-size:11px;color:var(--grey)}
.projects .loadmore{top:748px}

/* services */
.green{background:linear-gradient(135deg,#9fd24c 0%,#86bd37 50%,#74a82b 100%);color:var(--ink-2)}
.services{top:1620px;height:452px}
.cols4{left:160px;top:220px;width:880px;display:grid;grid-template-columns:repeat(4,1fr);gap:20px;text-align:center}
.cols4 svg{display:block;margin:0 auto 12px}
.cols4 h3{font-size:13px;font-weight:700;margin-bottom:6px}
.cols4 p{font-size:10px;line-height:1.5}

/* news */
.dark{background:var(--ink);color:var(--white)}
.news{top:2072px;height:560px}
.cards3{left:160px;top:208px;width:880px;display:grid;grid-template-columns:repeat(3,1fr);gap:30px}
.news-card .img{height:150px;background:linear-gradient(135deg,#6b5a45,#3c3a36)}
.news-card:nth-child(2) .img{background:linear-gradient(135deg,#d9d3c2,#8a8574)}
.news-card:nth-child(3) .img{background:linear-gradient(135deg,#c5943e,#6b5320)}
.news-card h3{font-size:12px;color:var(--green);margin:12px 0 6px;font-weight:700}
.news-card h3 small{color:var(--white);font-size:10px}
.news-card p{font-size:10px;line-height:1.5;color:#ccc}
.btn{display:inline-flex;align-items:center;gap:8px;background:#3c3c3c;color:var(--white);font-size:10px;font-weight:700;padding:0 12px 0 0;height:24px;margin-top:12px}
.btn i{width:24px;height:24px;background:var(--green);display:flex;align-items:center;justify-content:center}

/* team */
.team{top:2632px;height:588px;background:var(--light)}
.members{left:160px;top:210px;width:880px;display:flex;justify-content:center;gap:170px;text-align:center}
.member .avatar{width:100px;height:100px;border-radius:50%;border:4px solid var(--green);background:linear-gradient(180deg,#dcdcdc,#9a9a9a);margin:0 auto 10px}
.member h3{font-size:12px;font-weight:600}
.member p{font-size:10px;color:var(--grey);margin-bottom:6px}
.member .social{justify-content:center}
.member .social i{background:#999}
.pager{left:0;right:0;top:400px;display:flex;justify-content:center;gap:4px}
.pager i{width:16px;height:16px;background:#bbb;display:block}
.pager i.on{background:var(--green)}

/* testimonials */
.testimonials{top:3220px;height:280px}
.testimonials h2{position:absolute;left:190px;top:40px;font-size:26px;font-weight:400;color:var(--white)}
.testimonials p{position:absolute;left:190px;top:90px;width:280px;font-size:11px;line-height:1.5;color:var(--white)}
.testimonials .fb{position:absolute;left:190px;top:176px;background:var(--ink);color:var(--white);font-size:10px;padding:6px 12px}
.testimonials .people{position:absolute;left:700px;top:20px;width:360px;height:260px;background:linear-gradient(180deg,#e5e1da,#3b3b3b)}

/* apartments */
.apartments{top:3500px;height:840px;background:var(--white)}
.apts{left:160px;top:110px;width:880px;display:grid;grid-template-columns:1fr 1fr;gap:30px 20px}
.apt{height:240px;display:flex;position:relative}
.apt .info{width:200px;background:var(--ink);color:var(--white);padding-bottom:10px;position:relative}
.apt .info h3{background:var(--green);color:var(--ink-2);font-size:14px;font-weight:700;padding:10px 14px;line-height:1.3}
.apt .info .sub{font-size:10px;padding:4px 14px;color:#ccc}
.apt .info p{font-size:10px;line-height:1.5;padding:8px 14px 0;color:#ccc}
.apt .info .btn{position:absolute;left:14px;bottom:14px;background:#3c3c3c}
.apt .photo{flex:1;background:linear-gradient(135deg,#5a5a5a,#1f1f1f)}
.apt:nth-child(2) .photo{background:linear-gradient(135deg,#cfd6dd,#6c6f70)}
.apt:nth-child(3) .photo{background:linear-gradient(135deg,#7a6650,#2a2420)}
.apt:nth-child(4) .photo{background:linear-gradient(135deg,#a98558,#4a3d2e)}
.apartments .loadmore{top:652px}

/* clients */
.clients{top:4340px;height:200px;background:var(--white);border-top:1px solid #eee}
.clients h2{position:absolute;left:0;right:0;top:24px;text-align:center;font-size:22px;font-weight:400}
.logos{left:160px;top:96px;width:880px;display:flex;justify-content:space-between;align-items:center;font-size:22px;font-weight:700;color:var(--ink)}

/* contact */
.contact-sec{top:4540px;height:300px;background:var(--light)}
.contact-sec h2{position:absolute;left:160px;top:40px;font-size:26px;font-weight:400}
.contact-sec .intro{position:absolute;left:160px;top:84px;width:300px;font-size:10px;line-height:1.5;color:var(--grey)}
.contact-list{position:absolute;left:160px;top:146px;font-size:11px;line-height:2.3}
.contact-list li{list-style:none;display:flex;align-items:center;gap:10px}
.form{position:absolute;left:740px;top:40px;width:300px}
.field{height:28px;background:var(--white);border:1px solid var(--line);font-size:10px;color:var(--grey);padding:7px 10px;margin-bottom:8px;display:flex;justify-content:space-between}
.field.msg{height:130px}
.send{position:absolute;right:0;top:196px;background:var(--ink);color:var(--white);font-size:10px;padding:8px 14px}

/* footer */
.footer{top:4840px;height:380px;background:var(--ink-3);color:var(--white)}
.fcol{position:absolute;top:40px}
.fcol h3{font-size:18px;font-weight:400;margin-bottom:18px}
.sitemap li{list-style:none;font-size:11px;line-height:2.4;color:#bbb;border-bottom:1px solid #333;width:180px}
.sitemap li.on{color:var(--green)}
.feed{display:flex;gap:10px;margin-bottom:14px}
.feed i{width:38px;height:38px;background:#555;display:block;flex:none}
.feed p{font-size:10px;color:#bbb;line-height:1.4;width:150px}
.feed p b{color:var(--green);font-weight:600}
.sub-field{width:220px;height:28px;border:1px solid var(--green);font-size:10px;color:#888;padding:7px 10px;margin-bottom:8px}
.sub-btn{display:inline-block;background:var(--green);color:var(--ink-2);font-size:10px;font-weight:700;padding:7px 14px}

.copy{top:5220px;height:88px;background:var(--white);border-top:4px solid var(--green)}
.copy .l{position:absolute;left:160px;top:34px;font-size:10px;color:var(--grey)}
.copy .r{position:absolute;right:160px;top:34px;font-size:10px;color:var(--grey)}
.copy .up{position:absolute;left:576px;top:-30px;width:48px;height:40px;background:var(--ink);display:flex;align-items:center;justify-content:center}
</style>
</head>
<body>

<header class="section topbar">
  <div class="abs contact">
    <span><svg width="12" height="9" viewBox="0 0 12 9"><rect x=".5" y=".5" width="11" height="8" fill="none" stroke="#8dc63f"/><path d="M.5 .5 6 5 11.5 .5" fill="none" stroke="#8dc63f"/></svg>hello@lanterndwelling.com</span>
    <span><svg width="10" height="10" viewBox="0 0 10 10"><path d="M2 0 4 3 3 4c1 1.5 2 2.5 3 3l1-1 3 2-1 2C5 10 0 5 0 1z" fill="#8dc63f"/></svg>(612) 555-0148</span>
  </div>
  <div class="social"><i></i><i></i><i></i><i></i><i></i><i></i></div>
</header>

<nav class="section nav">
  <div class="abs logo"><b>Lantern Dwelling</b><small>PARTNERS · REAL ESTATE</small></div>
  <div class="abs menu">
    <a class="active">HOME</a><a>BUY</a><a>SELL</a><a>INVESTOR</a><a>SERVICES</a><a>ABOUT</a><a>CONTACT US</a>
  </div>
</nav>

<section class="section hero" role="img" aria-label="Photo of a modern residential tower among green trees under a soft evening sky">
  <div class="abs arrow" style="left:0"></div>
  <div class="abs arrow right"></div>
  <div class="caption">
    <h2>Some tagline Goes here</h2>
    <p>Warm furnished homes in the most desirable neighbourhoods,<br>chosen with care for every guest and client.</p>
  </div>
  <div class="dots"><i class="on"></i><i></i><i></i><i></i><i></i></div>
</section>

<section class="section projects">
  <div class="title" style="top:64px">
    <h2>Our Projects</h2>
    <p>Homes we have furnished, sold and managed across the city,<br>each shaped around the people who live there.</p>
  </div>
  <div class="filters"><span class="on">All</span><span>Residential</span><span>Industrial</span><span>Reporting</span><span>Others</span></div>
  <div class="abs grid">
    <div role="img" aria-label="Photo of a glass office tower"></div>
    <div role="img" aria-label="Photo of high rise apartment buildings"></div>
    <div role="img" aria-label="Photo of a city skyline at dusk"></div>
    <div role="img" aria-label="Photo of a tall residential block"></div>
    <div class="hover" role="img" aria-label="Photo of a plaza with a zoom and link overlay">
      <svg width="26" height="26" viewBox="0 0 26 26"><circle cx="11" cy="11" r="7" fill="none" stroke="#8dc63f" stroke-width="2.5"/><path d="M16 16 23 23" stroke="#8dc63f" stroke-width="3"/></svg>
      <svg width="24" height="24" viewBox="0 0 24 24"><rect x="2" y="9" width="12" height="6" rx="3" fill="none" stroke="#fff" stroke-width="2"/><rect x="10" y="9" width="12" height="6" rx="3" fill="none" stroke="#fff" stroke-width="2"/></svg>
    </div>
    <div role="img" aria-label="Photo of a waterfront house with reflections"></div>
  </div>
  <div class="abs loadmore">Load More Photos</div>
</section>

<section class="section services green">
  <div class="title" style="top:64px">
    <h2>Services we provide</h2>
    <p>From short stays to lasting homes, we guide buyers, sellers and investors through<br>every step with local knowledge and a personal approach.</p>
  </div>
  <div class="abs cols4">
    <div><svg width="48" height="48" viewBox="0 0 48 48"><circle cx="24" cy="24" r="22" fill="none" stroke="#222" stroke-width="2"/><path d="M14 25 24 16 34 25M17 23v10h14V23" fill="none" stroke="#222" stroke-width="2"/></svg><h3>Service Title</h3><p>Furnished homes matched to each guest, ready for a stay of any length.</p></div>
    <div><svg width="48" height="48" viewBox="0 0 48 48"><circle cx="24" cy="24" r="22" fill="none" stroke="#222" stroke-width="2"/><circle cx="24" cy="22" r="5" fill="none" stroke="#222" stroke-width="2"/><path d="M24 27v8" stroke="#222" stroke-width="2"/></svg><h3>Service Title</h3><p>Careful guidance for sellers, from pricing to the final signed papers.</p></div>
    <div><svg width="48" height="48" viewBox="0 0 48 48"><circle cx="24" cy="24" r="22" fill="none" stroke="#222" stroke-width="2"/><path d="M16 32 30 18M28 16l4 4" stroke="#222" stroke-width="2.5"/></svg><h3>Service Title</h3><p>Hands on support for investors building a strong rental portfolio.</p></div>
    <div><svg width="48" height="48" viewBox="0 0 48 48"><circle cx="24" cy="24" r="22" fill="none" stroke="#222" stroke-width="2"/><path d="M17 24h14M24 17v14" stroke="#222" stroke-width="2.5"/></svg><h3>Service Title</h3><p>Local insight on the areas, schools and streets our clients love most.</p></div>
  </div>
</section>

<section class="section news dark">
  <div class="title" style="top:64px">
    <h2>Latest News</h2>
    <p>Updates from our team on listings, market movement and new homes<br>across the neighbourhoods we serve every day.</p>
  </div>
  <div class="abs cards3">
    <article class="news-card"><div class="img" role="img" aria-label="Photo of a building site with machinery"></div><h3>Latest News Title, <small>Dec 21 2015</small></h3><p>New furnished suites open this winter near the river, with flexible leases for families and working guests.</p><span class="btn"><i><svg width="12" height="10" viewBox="0 0 12 10"><path d="M1 5 4.5 8.5 11 1" fill="none" stroke="#fff" stroke-width="2"/></svg></i>Read More</span></article>
    <article class="news-card"><div class="img" role="img" aria-label="Photo of builders in hard hats reviewing plans"></div><h3>Latest News Title, <small>Dec 21 2015</small></h3><p>Our team reviews the new housing plans and shares what buyers can expect from the coming season.</p><span class="btn"><i><svg width="12" height="10" viewBox="0 0 12 10"><path d="M1 5 4.5 8.5 11 1" fill="none" stroke="#fff" stroke-width="2"/></svg></i>Read More</span></article>
    <article class="news-card"><div class="img" role="img" aria-label="Photo of a worker fitting a new home interior"></div><h3>Latest News Title, <small>Dec 21 2015</small></h3><p>Small upgrades that add warmth and value to a rental home, chosen by our most trusted partners.</p><span class="btn"><i><svg width="12" height="10" viewBox="0 0 12 10"><path d="M1 5 4.5 8.5 11 1" fill="none" stroke="#fff" stroke-width="2"/></svg></i>Read More</span></article>
  </div>
</section>

<section class="section team">
  <div class="title" style="top:64px;color:#2b2b2b">
    <h2>Our Team</h2>
    <p>The people behind every home we place, sell and care for.</p>
  </div>
  <div class="abs members">
    <div class="member"><div class="avatar" role="img" aria-label="Portrait of a team member"></div><h3>Mark Ellison</h3><p>Designation goes here</p><div class="social"><i></i><i></i><i></i></div></div>
    <div class="member"><div class="avatar" role="img" aria-label="Portrait of a team member"></div><h3>Mark Ellison</h3><p>Designation goes here</p><div class="social"><i></i><i></i><i></i></div></div>
    <div class="member"><div class="avatar" role="img" aria-label="Portrait of a team member"></div><h3>Mark Ellison</h3><p>Designation goes here</p><div class="social"><i></i><i></i><i></i></div></div>
  </div>
  <div class="abs pager"><i></i><i class="on"></i></div>
</section>

<section class="section testimonials green">
  <h2>Testimonials</h2>
  <p>They found us the perfect home within a week and handled every detail with real care. We felt welcome from the very first day. — Happy Client</p>
  <span class="fb">Feedback By</span>
  <div class="people" role="img" aria-label="Photo of a smiling businessman and a colleague presenting"></div>
</section>

<section class="section apartments">
  <div class="title" style="top:32px">
    <h2>Apartments for Sale</h2>
    <p>Hand picked homes ready for new owners in the city's most loved areas.</p>
  </div>
  <div class="abs apts">
    <div class="apt"><div class="info"><h3>Name &amp; Address<br>of the Apartment</h3><div class="sub">Address line goes here</div><p>Bright rooms, modern kitchen and a quiet street close to parks and shops.</p><span class="btn"><i><svg width="10" height="10" viewBox="0 0 10 10"><path d="M3 1 7 5 3 9" fill="none" stroke="#fff" stroke-width="2"/></svg></i>Read More</span></div><div class="photo" role="img" aria-label="Photo of a dark modern living room"></div></div>
    <div class="apt"><div class="info"><h3>Name &amp; Address<br>of the Apartment</h3><div class="sub">Address line goes here</div><p>Clean lines, tall windows and a sunny terrace on a calm corner lot.</p><span class="btn"><i><svg width="10" height="10" viewBox="0 0 10 10"><path d="M3 1 7 5 3 9" fill="none" stroke="#fff" stroke-width="2"/></svg></i>Read More</span></div><div class="photo" role="img" aria-label="Photo of a white modern house exterior"></div></div>
    <div class="apt"><div class="info"><h3>Name &amp; Address<br>of the Apartment</h3><div class="sub">Address line goes here</div><p>Open kitchen and dining space with warm wood and soft lighting.</p><span class="btn"><i><svg width="10" height="10" viewBox="0 0 10 10"><path d="M3 1 7 5 3 9" fill="none" stroke="#fff" stroke-width="2"/></svg></i>Read More</span></div><div class="photo" role="img" aria-label="Photo of a kitchen and dining interior"></div></div>
    <div class="apt"><div class="info"><h3>Name &amp; Address<br>of the Apartment</h3><div class="sub">Address line goes here</div><p>Spacious lounge with large windows looking out over the gardens.</p><span class="btn"><i><svg width="10" height="10" viewBox="0 0 10 10"><path d="M3 1 7 5 3 9" fill="none" stroke="#fff" stroke-width="2"/></svg></i>Read More</span></div><div class="photo" role="img" aria-label="Photo of a warm living room with sofas"></div></div>
  </div>
  <div class="abs loadmore">Load More Apartments</div>
</section>

<section class="section clients">
  <h2>Prospective Clients</h2>
  <div class="abs logos"><span>Aerolis</span><span>Veltrano</span><span>Skyhaven</span><span>Norvik</span><span>Crestline</span></div>
</section>

<section class="section contact-sec">
  <h2>Contact Us :</h2>
  <p class="intro">Reach our team any day of the week for viewings, questions or a fresh start in a new home.</p>
  <ul class="contact-list">
    <li><svg width="12" height="14" viewBox="0 0 12 14"><path d="M6 0a5 5 0 0 1 5 5c0 4-5 9-5 9S1 9 1 5a5 5 0 0 1 5-5z" fill="#2b2b2b"/><circle cx="6" cy="5" r="2" fill="#f3f3f3"/></svg>420 Linden Avenue, Suite 12, Minneapolis MN</li>
    <li><svg width="12" height="12" viewBox="0 0 10 10"><path d="M2 0 4 3 3 4c1 1.5 2 2.5 3 3l1-1 3 2-1 2C5 10 0 5 0 1z" fill="#2b2b2b"/></svg>Phone: (612) 555-0148</li>
    <li><svg width="12" height="12" viewBox="0 0 12 12"><rect x="1" y="3" width="10" height="7" fill="#2b2b2b"/><rect x="3" y="0" width="6" height="3" fill="#2b2b2b"/></svg>Fax: (612) 555-0192</li>
    <li><svg width="12" height="9" viewBox="0 0 12 9"><rect width="12" height="9" fill="#2b2b2b"/><path d="M0 0 6 5 12 0" fill="none" stroke="#f3f3f3"/></svg>Email: hello@lanterndwelling.com</li>
  </ul>
  <div class="form">
    <div class="field">Your Name<span>&#9679;</span></div>
    <div class="field">Email<span>&#9993;</span></div>
    <div class="field msg">Message</div>
    <span class="send">Send Message</span>
  </div>
</section>

<footer class="section footer">
  <div class="fcol" style="left:160px"><h3>Sitemap</h3>
    <ul class="sitemap"><li class="on">Home</li><li>Buy</li><li>Sell</li><li>Investor</li><li>Services</li><li>About us</li><li>Contact</li></ul>
  </div>
  <div class="fcol" style="left:460px"><h3>Recent Feedback</h3>
    <div class="feed"><i role="img" aria-label="Client thumbnail"></i><p><b>Great stay and kind staff,</b> we will be back next year. <br>June 12, 2015</p></div>
    <div class="feed"><i role="img" aria-label="Client thumbnail"></i><p><b>Smooth sale from start to end,</b> thank you all. <br>June 12, 2015</p></div>
    <div class="feed"><i role="img" aria-label="Client thumbnail"></i><p><b>The apartment felt like home,</b> warm and quiet. <br>June 12, 2015</p></div>
  </div>
  <div class="fcol" style="left:780px"><h3>Subscribe Us</h3>
    <div class="sub-field">Your Name</div>
    <div class="sub-field">Email Id</div>
    <span class="sub-btn">Subscribe</span>
  </div>
</footer>

<div class="section copy">
  <div class="up"><svg width="16" height="10" viewBox="0 0 16 10"><path d="M1 9 8 2 15 9" fill="none" stroke="#fff" stroke-width="2.5"/></svg></div>
  <span class="l">Copyright © 2015 Lantern Dwelling Partners</span>
  <span class="r">Terms &amp; Privacy Policy</span>
</div>

</body>
</html>
```